2018 Vision Board Workshop

I need to promote this workshop on both an 8.5x11 sheet and a 5x7 card. I do have a logo that needs to be present. I'd like to stay true to my branded colors. The flyer needs to project the excitement of a new year and the possibilities of what a person can create, produce, explore in their lives by putting it all on a vision board. Creating the vision of what you want will inspire you to achieve your goals and dreams. Looking at your vision board each day will propel you into taking action as you chart your course to achieve what you truly want.
The flyer needs to have the following information:
The workshop date and time - Sat., Jan. 13, 2018, 10:30-1:30
The location is - Studio 47B, 2486 Maple Ridge Ln, Colorado Springs, Co 80920
in the BUILD Room
My name and contact information - Mara Lindqvist
Text and voice 303-614-7752
Email - mara@bright-path-forward.com
Website - bright-path-forward.com
The fee is $45. All materials are provided.

My company is called Bright Path Forward. I am a Life Coach, author, speaker and workshop leader.\ I wrote this program, Bright Path Forward to teach concepts and supporting skills for living with more happiness, satisfaction and fulfillment. Thanks for reading this!! Mara

Target Market(s)

Primarily women, educated, motivated, proactive in their own lives and well being

Font styles to use
Other font styles liked:
• I have been using Century Gothic. I'm open to new ideas.

Requirements
Must have
• The Bright Path Forward logo
• The flyer needs to have the following information:
• The workshop date and time - Sat., Jan. 13, 2018, 10:30-1:30
• The location is - Studio 47B, 2486 Maple Ridge Ln, Colorado Springs, Co 80920
• in the BUILD Room
• My name and contact information - Mara Lindqvist
• Text and voice 303-614-7752
• Email - mara@bright-path-forward.com
• Website - bright-path-forward.com
• The fee is $45. All materials are provided.
Nice to have
• The Bright Path Forward branded colors in the design
• Images of vision boards

```html
<!DOCTYPE html>
<html lang="en">
<head>
<meta charset="utf-8">
<title>2018 Vision Board Workshop</title>
<link rel="stylesheet" href="https://fonts.googleapis.com/css2?family=Questrial&family=Didact+Gothic&family=Oswald:wght@500&family=Lobster&family=Great+Vibes&family=Comfortaa:wght@500&family=Rye&display=swap">
<style>
:root{
  --green:#8dc63f;
  --band:#9ccb3b;
  --blue:#3aa6dd;
  --pink:#e5157a;
  --orange:#f7941d;
  --yellow:#f2ec55;
  --note-green:#6cbf3a;
  --dark:#3b3b3b;
  --text:#5f5f5f;
  --ink:#1e1e1e;
  --cork:#a8672f;
  --page:#e8e8e8;
}
*{margin:0;padding:0;box-sizing:border-box}
html,body{width:979px;height:1200px;overflow:hidden;background:var(--page)}
.flyer{position:absolute;left:26px;top:0;width:926px;height:1200px;background:#fff;overflow:hidden;font-family:"Questrial",sans-serif}
.wash{position:absolute;left:0;top:0;width:926px;height:200px;background:linear-gradient(120deg,#dfeed8 0%,#f3f8ee 40%,#fff 70%)}
.collage{position:absolute;left:0;top:0;width:926px;height:680px}
.cork{position:absolute;inset:0;clip-path:polygon(0 75px,926px 0,926px 545px,0 623px);
  background:radial-gradient(circle at 30% 40%,#b97a3e,transparent 60%),radial-gradient(circle at 75% 70%,#8f5424,transparent 55%),var(--cork)}
.photo{position:absolute;border:5px solid #fff;box-shadow:0 3px 6px rgba(0,0,0,.35)}
.note{position:absolute;display:flex;align-items:center;justify-content:center;box-shadow:0 3px 6px rgba(0,0,0,.35);text-align:center;line-height:1}
.note--green{background:var(--note-green);color:#fff}
.note--blue{background:var(--blue);color:#fff}
.note--dark{background:var(--dark);color:#fff}
.note--yellow{background:var(--yellow);color:#2f7d32}
.note--orange{background:var(--orange);color:#e5157a}
.note--pink{background:var(--pink);color:#fff}
.f-block{font-family:"Oswald",sans-serif;font-weight:500}
.f-round{font-family:"Comfortaa",sans-serif}
.f-script{font-family:"Lobster",cursive}
.f-fine{font-family:"Great Vibes",cursive}
.f-west{font-family:"Rye",serif}
.fee{position:absolute;left:744px;top:484px;width:152px;height:152px}
.fee-text{position:absolute;left:744px;top:484px;width:152px;height:152px;display:flex;align-items:center;justify-content:center;text-align:center;color:#fff;font-size:17px;line-height:1.35}
.brand{position:absolute;left:0;width:926px;text-align:center}
.brand-mark{top:634px;display:flex;justify-content:center}
.brand-mark span{width:22px;height:22px;border-radius:50%;background:var(--green)}
.brand-name{top:658px;font-size:48px;color:var(--green);font-family:"Didact Gothic",sans-serif}
.intro{position:absolute;top:748px;left:20px;width:886px;text-align:center;font-size:20.5px;line-height:25.5px;color:var(--text);white-space:nowrap}
.title{position:absolute;top:838px;left:0;width:926px;display:flex;align-items:center;justify-content:center;gap:22px;font-size:31px;font-weight:normal;color:var(--green)}
.title::before,.title::after{content:"";width:126px;height:1.5px;background:#444}
.when{position:absolute;top:898px;left:60px;width:818px;height:67px;border:2px solid var(--green);display:flex;align-items:center;justify-content:center;font-size:30px;color:var(--ink)}
.where{position:absolute;top:993px;left:250px;width:440px;text-align:center;font-size:19px;line-height:24px;color:var(--text)}
.band{position:absolute;left:0;top:1065px;width:926px;height:135px;background:var(--band)}
.portrait{position:absolute;left:42px;top:975px;width:160px;height:160px;border-radius:50%;border:5px solid #fff;box-shadow:0 0 0 2px #d8d8d8;background:radial-gradient(circle at 50% 45%,#e9b992,#c98a43 60%,#8a5a22)}
.host{position:absolute;top:1082px;left:230px;width:490px;text-align:center;font-size:39px;color:#fff}
.contacts{position:absolute;top:1143px;left:0;width:926px;height:28px;color:#fff;font-family:"Didact Gothic",sans-serif;font-weight:bold;font-size:19px}
.contact{position:absolute;display:flex;align-items:center;gap:7px;white-space:nowrap}
.contact svg{width:19px;height:19px}
</style>
</head>
<body>
<main class="flyer">
  <div class="wash" role="img" aria-label="Soft green watercolour wash"></div>

  <section class="collage">
    <div class="cork" role="img" aria-label="Cork vision board background"></div>

    <div class="photo" role="img" aria-label="Photo of a large stone house" style="left:130px;top:88px;width:196px;height:222px;transform:rotate(-4deg);background:linear-gradient(#b8d3ea,#8a7a5c 45%,#5d7a3a)"></div>
    <div class="photo" role="img" aria-label="Photo of money bags with currency symbols" style="left:384px;top:40px;width:193px;height:118px;transform:rotate(-8deg);background:linear-gradient(#fff,#d8c6a2 60%,#a98d5e)"></div>
    <div class="photo" role="img" aria-label="Photo of a happy family hugging" style="left:653px;top:22px;width:223px;height:158px;transform:rotate(-3deg);background:linear-gradient(135deg,#d9c2a8,#8a6248 55%,#5d4a3d)"></div>
    <div class="photo" role="img" aria-label="Photo of a white luxury car" style="left:669px;top:294px;width:240px;height:158px;transform:rotate(-4deg);background:linear-gradient(#fff,#f1f1f1 55%,#bfbfbf)"></div>
    <div class="photo" role="img" aria-label="Photo of a family walking on a beach" style="left:261px;top:300px;width:327px;height:262px;transform:rotate(-6deg);background:linear-gradient(#4f9fdb,#8fd0ef 45%,#f4ecdf 60%,#efe4d0)"></div>
    <div class="photo" role="img" aria-label="Photo of a couple cycling outdoors" style="left:15px;top:406px;width:202px;height:138px;transform:rotate(-2deg);background:linear-gradient(135deg,#9cc275,#5f8a3a 60%,#3f5f28)"></div>

    <div class="note note--green f-block" style="left:0;top:96px;width:124px;height:62px;font-size:30px;transform:rotate(-5deg)">Happiness</div>
    <div class="note note--blue f-round" style="left:231px;top:78px;width:134px;height:52px;font-size:28px;transform:rotate(-5deg)">comfort</div>
    <div class="note note--dark f-block" style="left:10px;top:274px;width:125px;height:72px;font-size:27px;transform:rotate(-3deg)">SUCCESS</div>
    <div class="note note--yellow f-west" style="left:338px;top:178px;width:136px;height:90px;font-size:21px;transform:rotate(-14deg);flex-direction:column">Financial<br>Freedom</div>
    <div class="note note--orange f-block" style="left:514px;top:146px;width:112px;height:80px;font-size:30px;transform:rotate(-6deg)">SECURITY</div>
    <div class="note note--dark f-block" style="left:786px;top:18px;width:94px;height:52px;font-size:26px;transform:rotate(-6deg)">Wealth</div>
    <div class="note note--pink f-block" style="left:713px;top:168px;width:182px;height:76px;font-size:30px;transform:rotate(-7deg)">Relationships</div>
    <div class="note note--green f-block" style="left:607px;top:235px;width:87px;height:64px;font-size:26px;transform:rotate(-3deg)">PEACE</div>
    <div class="note note--yellow f-script" style="left:514px;top:308px;width:128px;height:82px;font-size:40px;transform:rotate(-5deg)">Family</div>
    <div class="note note--blue f-fine" style="left:751px;top:412px;width:164px;height:82px;font-size:46px;transform:rotate(-8deg)">Luxury</div>
    <div class="note note--green f-round" style="left:159px;top:330px;width:156px;height:66px;font-size:29px;transform:rotate(-6deg)">wellness</div>
    <div class="note note--pink f-script" style="left:437px;top:478px;width:200px;height:80px;font-size:42px;transform:rotate(-5deg)">Vacations</div>
    <div class="note note--orange f-block" style="left:62px;top:500px;width:128px;height:96px;font-size:40px;transform:rotate(-3deg)">Health</div>

    <svg class="fee" viewBox="0 0 152 152" aria-hidden="true">
      <polygon fill="#9ccb3b" points="76,0 83,14 94,2 97,17 110,8 109,23 124,18 119,32 135,31 127,44 143,47 132,58 148,64 135,72 150,80 135,86 147,97 131,100 140,113 124,113 129,127 114,124 115,140 101,133 98,149 87,138 80,152 72,139 63,151 56,137 45,147 43,132 30,139 31,124 16,127 21,113 6,112 15,100 1,94 13,86 0,77 14,70 2,61 17,56 8,44 23,43 17,29 32,31 29,16 43,22 44,7 57,16 62,2 69,15"/>
    </svg>
    <div class="fee-text">The fee is $45.<br>All materials<br>are provided.</div>
  </section>

  <div class="brand brand-mark"><span></span></div>
  <div class="brand brand-name">Bright Path Forward</div>

  <p class="intro">Creating the vision of what you want will inspire you to achieve your goals and<br>dreams. Looking at your vision board each day will propel you into taking action<br>as you chart your course to achieve what you truly want.</p>

  <h1 class="title">2018 Vision Board Workshop</h1>
  <div class="when">Saturay, January 13, 2018, 10:30-1:30</div>
  <p class="where">Studio 47B, 2486 Maple Ridge<br>Ln, Colorado Springs, Co 80920</p>

  <div class="band"></div>
  <div class="portrait" role="img" aria-label="Portrait photo of the workshop host"></div>
  <div class="host">Mara Lindqvist</div>

  <div class="contacts">
    <div class="contact" style="left:70px">
      <svg viewBox="0 0 20 20" aria-hidden="true"><circle cx="10" cy="10" r="8.5" fill="none" stroke="#fff" stroke-width="1.6"/><rect x="5.5" y="7" width="9" height="6.5" fill="none" stroke="#fff" stroke-width="1.3"/><path d="M5.5 7l4.5 3.5 4.5-3.5" fill="none" stroke="#fff" stroke-width="1.3"/></svg>
      mara@bright-path-forward.com
    </div>
    <div class="contact" style="left:400px">
      <svg viewBox="0 0 20 20" aria-hidden="true"><circle cx="10" cy="10" r="8.5" fill="none" stroke="#fff" stroke-width="1.6"/><path d="M7 5.5l1.6 2.6-1 1.1c.7 1.4 1.7 2.4 3.1 3.1l1.1-1 2.6 1.6-.9 1.8c-3.6-.3-7.1-3.8-7.4-7.4z" fill="#fff"/></svg>
      303-614-7752
    </div>
    <div class="contact" style="left:598px">
      <svg viewBox="0 0 20 20" aria-hidden="true"><circle cx="10" cy="10" r="8.5" fill="none" stroke="#fff" stroke-width="1.6"/><circle cx="10" cy="10" r="5" fill="none" stroke="#fff" stroke-width="1.2"/><path d="M5 10h10M10 5c-2 2.8-2 7.2 0 10M10 5c2 2.8 2 7.2 0 10" fill="none" stroke="#fff" stroke-width="1.1"/></svg>
      www.bright-path-forward.com
    </div>
  </div>
</main>
</body>
</html>
```